Financial Advisor Resource Firm needs business card design

Need business card design for company in Omaha NE called Meridale Circle. We provide resources to financial advisors....workshop programs, retirement analysis, and insurance planning. I would like to see designs that use grays, greens, black, and white colors. The final design should communicate 'collaboration' and be simple yet attractive to financial planning clients. I will attached our logo and another picture of a puzzle piece coming together. I would like the incorporate the puzzle picture somehow, maybe on the back somehow, with color or just the gray scale....OR, the picture be the front of the card with 'Meridale' definition on it (see upload) and then company logo, employee name, title, address on the back (see ppt uploaded). The following disclosure needs to be included somewhere- Advisory services offered through Stonebrook Assets, LLC.
Updates

I uploaded a svg and ai file of the logo

Target Market(s)

Financial planning clients and financial advisors....so pretty diverse age range of about 40-70.

Industry/Entity Type

Financial Planning

Contact Information for Business Card

Tobias L. Fenwright, MBA
Founder/President
5287 E. Larkin Road
Suite 410
Bellcrest, NE 68190
Phone- (402) 555-0147
Cell- (402) 555-0183
Fax- (402) 555-0129
email- tobias@meridaleplan.example
web address- www.meridaleplan.example

Colors
1b1b1b
474747
d3d3d3
ffffff
9bcb3c
abd036

Requirements
Must have
• Must include logo provided, must be 2 sided, and must have disclosure...all of these items listed in project description

```html
<!DOCTYPE html>
<html lang="en">
<head>
<meta charset="utf-8">
<title>Meridale Circle — Business Card</title>
<link href="https://fonts.googleapis.com/css2?family=Merriweather:wght@400;700&family=Roboto:wght@400;500;700&display=swap" rel="stylesheet">
<style>
  :root {
    --ink: #1b1b1b;
    --charcoal: #474747;
    --silver: #d3d3d3;
    --paper: #ffffff;
    --green: #9bcb3c;
    --lime: #abd036;
    --stage: #2a2e33;
  }
  * { box-sizing: border-box; margin: 0; padding: 0; }
  html, body { width: 1200px; height: 900px; overflow: hidden; }
  body {
    background: var(--stage);
    font-family: "Roboto", Arial, sans-serif;
    position: relative;
  }
  .card {
    position: absolute;
    left: 250px;
    width: 700px;
    height: 400px;
    border-radius: 28px;
    overflow: hidden;
    background: var(--paper);
    box-shadow: 0 10px 30px rgba(0,0,0,.45);
  }
  .card--front { top: 35px; }
  .card--back { top: 465px; }

  /* Front side */
  .card__shapes { position: absolute; inset: 0; }
  .brand {
    position: absolute;
    top: 70px;
    left: 0;
    right: 0;
    display: flex;
    align-items: center;
    justify-content: center;
    gap: 16px;
  }
  .brand__dot {
    width: 30px; height: 30px;
    border-radius: 50%;
    background: var(--green);
  }
  .brand__name {
    font-family: "Merriweather", Georgia, serif;
    font-weight: 700;
    font-size: 52px;
    letter-spacing: 1px;
    color: var(--ink);
  }
  .web {
    position: absolute;
    right: 38px;
    top: 214px;
    font-weight: 700;
    font-size: 19px;
    color: var(--green);
  }
  .person {
    position: absolute;
    left: 36px;
    top: 222px;
    color: var(--ink);
  }
  .person__name {
    font-family: "Merriweather", Georgia, serif;
    font-weight: 700;
    font-size: 20px;
  }
  .person__title { font-size: 15px; margin-top: 3px; }
  .contacts {
    position: absolute;
    left: 36px;
    top: 300px;
    list-style: none;
    color: var(--paper);
    font-size: 15px;
  }
  .contacts li {
    display: flex;
    align-items: center;
    gap: 10px;
    height: 22px;
  }
  .contacts svg { width: 14px; height: 14px; fill: var(--green); flex: none; }
  .contacts .accent { color: var(--green); }
  .office {
    position: absolute;
    right: 38px;
    top: 300px;
    text-align: right;
    font-size: 15px;
    line-height: 22px;
  }
  .office__disclosure { color: var(--paper); font-weight: 500; }
  .office__address { color: var(--green); font-weight: 500; }

  /* Back side */
  .photo {
    position: absolute;
    left: 0; top: 0;
    width: 100%; height: 225px;
    background: linear-gradient(120deg, #3a3a3a 0%, #8a8a8a 45%, #cfcfcf 70%, #5a5a5a 100%);
  }
  .definition {
    position: absolute;
    left: 0; right: 0;
    top: 245px;
    text-align: center;
  }
  .definition__word {
    font-family: "Merriweather", Georgia, serif;
    font-weight: 700;
    font-size: 58px;
    letter-spacing: 4px;
    color: var(--ink);
  }
  .definition__meaning {
    margin-top: 6px;
    font-size: 17px;
    color: var(--ink);
  }
  .back-band {
    position: absolute;
    left: 0; right: 0; bottom: 0;
    height: 20px;
    background: var(--green);
  }
</style>
</head>
<body>

<section class="card card--front">
  <svg class="card__shapes" viewBox="0 0 700 400" aria-hidden="true">
    <rect x="0" y="248" width="700" height="152" fill="var(--ink)"/>
    <polygon points="0,210 300,210 336,290 0,290" fill="var(--green)"/>
    <polygon points="300,244 700,244 700,252 304,252" fill="var(--green)"/>
  </svg>

  <div class="brand">
    <span class="brand__dot"></span>
    <span class="brand__name">Meridale Circle</span>
  </div>

  <div class="web">www.meridaleplan.example</div>

  <div class="person">
    <div class="person__name">Tobias L. Fenwright, MBA</div>
    <div class="person__title">Founder/President</div>
  </div>

  <ul class="contacts">
    <li><svg viewBox="0 0 24 24"><path d="M6.6 10.8a15 15 0 0 0 6.6 6.6l2.2-2.2c.3-.3.7-.4 1-.2 1.1.4 2.3.6 3.6.6.6 0 1 .4 1 1V20c0 .6-.4 1-1 1A17 17 0 0 1 3 4c0-.6.4-1 1-1h3.5c.6 0 1 .4 1 1 0 1.3.2 2.5.6 3.6.1.3 0 .7-.2 1z"/></svg><span>(402) 555-0147</span></li>
    <li><svg viewBox="0 0 24 24"><path d="M7 1h10a2 2 0 0 1 2 2v18a2 2 0 0 1-2 2H7a2 2 0 0 1-2-2V3a2 2 0 0 1 2-2zm0 3v15h10V4z"/></svg><span>(402) 555-0183</span></li>
    <li><svg viewBox="0 0 24 24"><path d="M6 2h9l3 3v4h2a2 2 0 0 1 2 2v9a2 2 0 0 1-2 2H4a2 2 0 0 1-2-2v-9a2 2 0 0 1 2-2h2zm2 2v5h8V6h-2V4zm-2 9v2h4v-2zm0 4v2h4v-2z"/></svg><span>(402) 555-0129</span></li>
    <li><svg viewBox="0 0 24 24"><path d="M2 5h20v14H2zm2 2v.5l8 5 8-5V7z"/></svg><span>tobias@<span class="accent">meridaleplan</span>.example</span></li>
  </ul>

  <div class="office">
    <div class="office__disclosure">Advisory services offered<br>through Stonebrook Assets, LLC.</div>
    <div class="office__address">5287 E. Larkin Road<br>Suite 410, Bellcrest, NE 68190</div>
  </div>
</section>

<section class="card card--back">
  <div class="photo" role="img" aria-label="Grayscale photo of several hands joining puzzle pieces together"></div>
  <div class="definition">
    <div class="definition__word">MERIDALE</div>
    <p class="definition__meaning">: to come together and unite in common interest and focus.</p>
  </div>
  <div class="back-band"></div>
</section>

</body>
</html>
```